Redo a PPT pres. - Real Estate in Brazil - Socially equitable investments in Social Housing

We need to redo the presentation attached. It is an institutional presentation to attract local and foreign investors to invest in Brazilian Social Housing Projects structured by our company "TLR".
A middle class of 100 million, a housing deficit of 9M, a strong political will & positive income generation trends constitute grounds for a significant demand in social housing.
This make a perfect scheme for investors to invest in Brazilian Social Housing.
"TLR", is a consulting "boutique" focused in Brazilian real estate, specialized in structuring, analyzing and originating Brazilian social housing projects.
TLR is part of the group TLB. TLB is structured to create value through each step of the residential real estate business - structuring, financing, sales, marketing and technology.
We would like to see designs that use mainly the color blue. The final design should communicate financial safety and professionalism. In order to reach our needs, the designer will need to have basic understanding of finance and investment in order to highlight the most important information.
The idea is to receive back the PPT with each page redesigned and an homogeneous identity.
To all designers,
Target Market(s)
Institutional Investors and wealthy individuals
Industry/Entity Type
Residential
Look and feel

```html
<!DOCTYPE html>
<html lang="en">
<head>
<meta charset="utf-8">
<title>TLR – Title Here</title>
<link rel="stylesheet" href="https://fonts.googleapis.com/css2?family=Carlito:wght@400;700&family=Open+Sans:wght@700&display=swap">
<style>
  :root {
    --band-blue: #3f86e6;
    --band-blue-light: #6aa8f2;
    --band-photo-dark: #2f6fcf;
    --band-photo-light: #8cbef5;
    --title-blue: #1d6fae;
    --title-dark: #10202e;
    --rule-grey: #d4d4d4;
    --wash-grey: #ebebeb;
    --footer-navy: #0a2458;
    --footer-navy-dark: #06183d;
    --brand-blue: #5cc0ec;
    --white: #ffffff;
  }
  * { margin: 0; padding: 0; box-sizing: border-box; }
  html, body { width: 1200px; height: 900px; overflow: hidden; background: var(--white); }
  .slide { position: relative; width: 1200px; height: 900px; overflow: hidden; background: var(--white); }
  .header-band {
    position: absolute; left: 0; top: 0; width: 1200px; height: 115px;
    background: linear-gradient(90deg, var(--band-blue) 0%, var(--band-blue-light) 60%, var(--band-blue) 100%);
  }
  .header-photo {
    position: absolute; right: 0; top: 0; width: 520px; height: 115px;
    background: linear-gradient(90deg, rgba(106,168,242,0) 0%, var(--band-photo-light) 30%, var(--band-photo-dark) 100%);
  }
  .title-wash {
    position: absolute; left: 0; top: 234px; width: 1200px; height: 130px;
    border-top: 2px solid var(--rule-grey);
    background: linear-gradient(180deg, var(--wash-grey) 0%, rgba(255,255,255,0) 100%);
  }
  .slide-title {
    position: absolute; left: 30px; top: 178px;
    font-family: "Carlito", "Calibri", sans-serif; font-weight: 700; font-size: 41px;
    color: var(--title-dark);
  }
  .slide-title .accent { color: var(--title-blue); margin-right: 10px; }
  .cycle-diagram { position: absolute; left: 560px; top: 110px; width: 640px; height: 660px; }
  .cycle-label { font-family: "Open Sans", sans-serif; font-weight: 700; font-size: 20px; fill: var(--white); letter-spacing: 0.5px; }
  .hub-label { font-family: "Open Sans", sans-serif; font-weight: 700; font-size: 23px; fill: var(--white); }
  .footer-band {
    position: absolute; left: 0; top: 757px; width: 1200px; height: 143px;
    background: linear-gradient(180deg, var(--footer-navy) 0%, var(--footer-navy-dark) 100%);
  }
  .brand-name {
    position: absolute; left: 28px; top: 770px;
    font-family: "Carlito", "Calibri", sans-serif; font-weight: 400; font-size: 86px;
    color: var(--brand-blue); line-height: 1;
  }
</style>
</head>
<body>
<main class="slide">
  <div class="header-band">
    <div class="header-photo" role="img" aria-label="Photo of glass office towers in blue tones"></div>
  </div>

  <div class="title-wash"></div>
  <h1 class="slide-title"><span class="accent">Title</span>Here</h1>

  <svg class="cycle-diagram" viewBox="560 110 640 660" xmlns="http://www.w3.org/2000/svg">
    <defs>
      <linearGradient id="arrow-fill" x1="0" y1="1" x2="1" y2="0">
        <stop offset="0" stop-color="#0f4aa8"/>
        <stop offset="0.6" stop-color="#1a6fd6"/>
        <stop offset="1" stop-color="#2eaaf2"/>
      </linearGradient>
      <radialGradient id="hub-ring" cx="0.5" cy="0.5" r="0.5">
        <stop offset="0.8" stop-color="#bfbfbf"/>
        <stop offset="1" stop-color="#e4e4e4"/>
      </radialGradient>
      <radialGradient id="hub-core" cx="0.5" cy="0.5" r="0.5">
        <stop offset="0.6" stop-color="#000000"/>
        <stop offset="1" stop-color="#3a3a3a"/>
      </radialGradient>
      <filter id="soft-shadow" x="-20%" y="-200%" width="140%" height="500%">
        <feGaussianBlur stdDeviation="8"/>
      </filter>
      <path id="label-path-1" d="M -212.7 -45.2 A 217.5 217.5 0 0 1 -45.2 -212.7"/>
      <path id="label-path-2" d="M 45.2 -212.7 A 217.5 217.5 0 0 1 212.7 -45.2"/>
      <path id="label-path-3" d="M 45.2 212.7 A 217.5 217.5 0 0 0 212.7 45.2"/>
      <path id="label-path-4" d="M -212.7 45.2 A 217.5 217.5 0 0 0 -45.2 212.7"/>
      <path id="cycle-arrow" d="M -270 0 A 270 270 0 0 1 -69.9 -260.8 L -75.1 -280.1 L 26.5 -215.9 L -37.5 -140.1 L -42.7 -159.4 A 165 165 0 0 0 -165 0 L -211 -52.6 Z" fill="url(#arrow-fill)" stroke="#ffffff" stroke-width="2"/>
    </defs>

    <ellipse class="diagram-shadow" cx="880" cy="740" rx="160" ry="10" fill="#9a9a9a" filter="url(#soft-shadow)"/>

    <g transform="translate(880 420)">
      <use href="#cycle-arrow"/>
      <use href="#cycle-arrow" transform="rotate(90)"/>
      <use href="#cycle-arrow" transform="rotate(180)"/>
      <use href="#cycle-arrow" transform="rotate(270)"/>

      <text class="cycle-label" dominant-baseline="central"><textPath href="#label-path-1" startOffset="50%" text-anchor="middle">YOUR TEXT HERE</textPath></text>
      <text class="cycle-label" dominant-baseline="central"><textPath href="#label-path-2" startOffset="50%" text-anchor="middle">YOUR TEXT HERE</textPath></text>
      <text class="cycle-label" dominant-baseline="central"><textPath href="#label-path-3" startOffset="50%" text-anchor="middle">YOUR TEXT HERE</textPath></text>
      <text class="cycle-label" dominant-baseline="central"><textPath href="#label-path-4" startOffset="50%" text-anchor="middle">YOUR TEXT HERE</textPath></text>

      <circle class="hub-ring" r="132" fill="url(#hub-ring)"/>
      <circle class="hub-core" r="108" fill="url(#hub-core)"/>
      <text class="hub-label" text-anchor="middle" y="-6">TITLE OF</text>
      <text class="hub-label" text-anchor="middle" y="24">DIAGRAM</text>
    </g>
  </svg>

  <footer class="footer-band"></footer>
  <div class="brand-name">TLR</div>
</main>
</body>
</html>
```